Classic and neutral book cover design

We are looking for a classic and neutral book cover design to be used as the template for a series of books to be published. We are hence looking for a template that will allow us to easily change the title name for all books in this series.
The use of very few colours (black and white is welcome) and few design elements is a big bonus. As a source of inspiration we would like to ask you to view the very simple and
If you think you have a cool idea that can add a twist to the formal classic look don't hesitate. Go for it !
Work will be done for a 30 year old Sweden based cultural non-profit called VĂ©ru (www.verufoundation.example). We work with the publishing and supporting of post-modern art and literature addressing contemporary topics but are also involved in assisting projects of cultural preservation.
Target Market(s)
The audience is expected to have some form of interest in culture but could range from hobbyist readers to tenure track scholars
Industry/Entity Type
Non-Profit
Requirements
Must have
- General:
- Classic and neutral feel
- Preferably very simple and few shapes
- usage of few colours (black and white is welcome)
Information to be displayed on the cover is:
- Author
- Title
- type of work e.g. play/novel (optional)
- publishing house (in this case "Veru Publishing")
Nice to have
- ideas to prevent it from become boring are of course welcome
Should not have
- - too many colours

```html
<!DOCTYPE html>
<html lang="lv">
<head>
<meta charset="utf-8">
<title>Revidents — book cover</title>
<link href="https://fonts.googleapis.com/css2?family=Gentium+Book+Plus&family=PT+Sans&display=swap" rel="stylesheet">
<style>
  :root {
    --backdrop: #efede8;
    --cover: #c8c6c1;
    --emblem-light: #c3c1bc;
    --emblem-dark: #b1afa9;
    --ink: #55534b;
    --ink-soft: #6f6d65;
    --shadow: rgba(0, 0, 0, 0.18);
  }
  html, body {
    margin: 0;
    width: 1200px;
    height: 1000px;
    overflow: hidden;
    background: var(--backdrop);
  }
  .canvas {
    position: relative;
    width: 1200px;
    height: 1000px;
  }
  .cover {
    position: absolute;
    left: 260px;
    top: 73px;
    width: 680px;
    height: 857px;
    background: var(--cover);
    box-shadow: 0 2px 6px var(--shadow);
  }
  .cover-emblem {
    position: absolute;
    left: 176px;
    top: 77px;
    width: 336px;
    height: 336px;
  }
  .author,
  .title,
  .genre,
  .separator,
  .publisher {
    position: absolute;
    left: 0;
    width: 100%;
    margin: 0;
    text-align: center;
    color: var(--ink);
  }
  .author {
    top: 464px;
    font: 27px/1 "Gentium Book Plus", serif;
  }
  .separator {
    top: 518px;
    font: 20px/1 "Gentium Book Plus", serif;
  }
  .title {
    top: 552px;
    font: 27px/1 "Gentium Book Plus", serif;
  }
  .genre {
    top: 588px;
    font: 15px/1 "Gentium Book Plus", serif;
    color: var(--ink-soft);
  }
  .publisher {
    top: 789px;
    font: 12px/1 "PT Sans", sans-serif;
    letter-spacing: 0.2px;
  }
</style>
</head>
<body>
  <main class="canvas">
    <section class="cover">
      <svg class="cover-emblem" viewBox="0 0 336 336" role="img" aria-label="Circular line emblem of interlaced rounded squares and ovals">
        <defs>
          <radialGradient id="emblem-tone" cx="50%" cy="50%" r="50%">
            <stop offset="0%" stop-color="var(--emblem-light)"/>
            <stop offset="100%" stop-color="var(--emblem-dark)"/>
          </radialGradient>
        </defs>
        <circle cx="168" cy="168" r="166" fill="url(#emblem-tone)"/>
      </svg>

      <p class="author">Matīss Ozolkalns</p>
      <p class="separator">*</p>
      <h1 class="title" style="font-weight:400">Revidents</h1>
      <p class="genre">luga</p>

      <p class="publisher">Veru Publishing</p>
    </section>
  </main>
</body>
</html>
```